BUSINESS CARD DESIGN

NAME- DALE VORSKIN
PHONE NUMER - 555- 714-9082
EMAIL- OFFICE@TRV-GROUNDMAKRZ.COM
BACK OF CARD- SPEACIALIZES IN LAND CLEARING, FORESTRY MUCLHING AND EXCAVATION

Contact Information for Business Card

NAME- DALE VORSKIN PHONE NUMER - 555- 714-9082 EMAIL- OFFICE@TRV-GROUNDMAKRZ.COM BACK OF CARD- SPEACIALIZES IN LAND CLEARING , MUCLHING AND EXCAVATION

```html
<!DOCTYPE html>
<html lang="en">
<head>
<meta charset="utf-8">
<title>Terravale Groundmakrz LLC – Business Card</title>
<link href="https://fonts.googleapis.com/css2?family=Orbitron:wght@600;800&display=swap" rel="stylesheet">
<style>
  :root {
    --backdrop: #d6d6d8;
    --card: #3a3a3c;
    --gold: #f5b82e;
    --band: #f7c531;
    --ink-dark: #2b2b2d;
  }
  html, body {
    margin: 0;
    width: 1200px;
    height: 897px;
    overflow: hidden;
    background: var(--backdrop);
    font-family: "Orbitron", sans-serif;
  }
  .canvas {
    position: relative;
    width: 1200px;
    height: 897px;
  }
  .card {
    position: absolute;
    left: 320px;
    width: 560px;
    height: 320px;
    background: var(--card);
    color: var(--gold);
    box-shadow: 0 10px 30px rgba(0,0,0,0.18);
  }
  .card--front { top: 100px; }
  .card--back  { top: 478px; }
  .band {
    position: absolute;
    left: 20%;
    width: 58%;
    height: 8px;
    background: var(--band);
  }
  .band--top { top: 0; }
  .band--bottom { bottom: 0; }

  .brand {
    display: flex;
    align-items: center;
    gap: 12px;
    font-weight: 800;
    color: var(--gold);
  }
  .brand__dot {
    width: 46px;
    height: 46px;
    border-radius: 50%;
    background: var(--gold);
    flex: none;
  }
  .brand__name {
    font-size: 13px;
    line-height: 1.3;
    letter-spacing: 0.05em;
  }
  .brand__phone {
    margin-top: 3px;
    font-size: 8px;
    letter-spacing: 0.35em;
  }
  .card--front .brand {
    position: absolute;
    left: 36px;
    top: 122px;
  }

  .card--back .back-content {
    position: absolute;
    left: 0;
    right: 0;
    top: 96px;
    display: flex;
    flex-direction: column;
    align-items: center;
  }
  .card--back .brand__name { font-size: 17px; }
  .card--back .brand__phone { font-size: 9px; }
  .specialties {
    margin: 34px 0 0;
    max-width: 420px;
    text-align: center;
    font-size: 11px;
    font-weight: 600;
    line-height: 1.7;
    letter-spacing: 0.08em;
  }

  .person {
    position: absolute;
    left: 300px;
    top: 78px;
  }
  .person__name {
    font-size: 22px;
    font-weight: 800;
    letter-spacing: 0.04em;
    margin: 0;
  }
  .person__role {
    display: inline-block;
    margin-top: 8px;
    padding: 3px 8px;
    background: var(--gold);
    color: var(--ink-dark);
    font-size: 13px;
    font-weight: 800;
    letter-spacing: 0.04em;
  }
  .contact {
    list-style: none;
    margin: 22px 0 0;
    padding: 0;
    font-size: 9.5px;
    font-weight: 600;
    letter-spacing: 0.03em;
  }
  .contact__item {
    display: flex;
    align-items: center;
    gap: 8px;
    margin-bottom: 9px;
  }
  .contact__icon {
    width: 11px;
    height: 11px;
    flex: none;
  }
</style>
</head>
<body>
<main class="canvas">

  <section class="card card--front" aria-label="Business card front">
    <div class="band band--top"></div>
    <div class="band band--bottom"></div>

    <div class="brand">
      <span class="brand__dot"></span>
      <div>
        <div class="brand__name">TERRAVALE<br>GROUNDMAKRZ LLC</div>
        <div class="brand__phone">555-714-9082</div>
      </div>
    </div>

    <div class="person">
      <h1 class="person__name">DALE VORSKIN</h1>
      <span class="person__role">OWNER</span>
      <ul class="contact">
        <li class="contact__item">
          <svg class="contact__icon" viewBox="0 0 12 12"><rect x="0.5" y="2" width="11" height="8" fill="none" stroke="currentColor"/><path d="M0.5 2 L6 7 L11.5 2" fill="none" stroke="currentColor"/></svg>
          OFFICE@TRV-GROUNDMAKRZ.COM
        </li>
        <li class="contact__item">
          <svg class="contact__icon" viewBox="0 0 12 12"><path d="M2.5 1 L4.5 1 L5.2 3.6 L3.8 4.6 C4.6 6.3 5.7 7.4 7.4 8.2 L8.4 6.8 L11 7.5 L11 9.5 C11 10.3 10.3 11 9.5 11 C5 11 1 7 1 2.5 C1 1.7 1.7 1 2.5 1 Z" fill="none" stroke="currentColor"/></svg>
          +555- 714-9082
        </li>
        <li class="contact__item">
          <svg class="contact__icon" viewBox="0 0 12 12"><circle cx="6" cy="6" r="5.2" fill="none" stroke="currentColor"/><ellipse cx="6" cy="6" rx="2.3" ry="5.2" fill="none" stroke="currentColor"/><path d="M0.8 6 H11.2" stroke="currentColor"/></svg>
          WWW.TRV-GROUNDMAKRZ.COM
        </li>
      </ul>
    </div>
  </section>

  <section class="card card--back" aria-label="Business card back">
    <div class="band band--top"></div>
    <div class="band band--bottom"></div>

    <div class="back-content">
      <div class="brand">
        <span class="brand__dot"></span>
        <div>
          <div class="brand__name">TERRAVALE<br>GROUNDMAKRZ LLC</div>
          <div class="brand__phone">555-714-9082</div>
        </div>
      </div>
      <p class="specialties">SPECIALIZES IN LAND CLEARING,<br>FORESTRY MULCHING AND EXCAVATION</p>
    </div>
  </section>

</main>
</body>
</html>
```